Need a website setup for our new removalist business.
Our business is called Harbour Lane Removals and would like a website setup.
We don’t have a website, logo or design as of yet. Our truck is blue so something possibly that works and can incorporate the blue.

```html
<!DOCTYPE html>
<html lang="en">
<head>
<meta charset="utf-8">
<title>Harbour Lane Removals</title>
<link rel="stylesheet" href="https://fonts.googleapis.com/css2?family=Poppins:wght@800&family=Roboto:ital,wght@0,400;0,500;0,700;1,400&display=swap">
<style>
:root{
  --blue:#0a9de2;
  --blue-dark:#0686c4;
  --navy:#16266b;
  --navy-deep:#0d1a52;
  --ink:#111418;
  --text:#4a4f57;
  --muted:#5c6470;
  --gold:#f0c419;
  --white:#ffffff;
}
*{box-sizing:border-box;margin:0;padding:0}
html,body{width:1200px;height:3506px;overflow:hidden;background:var(--white)}
body{position:relative;font-family:"Roboto",Arial,sans-serif;color:var(--text)}
.abs{position:absolute}
.heading{font-family:"Poppins",Arial,sans-serif;font-weight:800;color:var(--ink);letter-spacing:-1px;text-transform:uppercase}
.btn{position:absolute;display:flex;align-items:center;justify-content:center;border-radius:30px;font-weight:500;font-size:14px;text-transform:uppercase;text-decoration:none}
.btn-solid{background:var(--blue);color:var(--white)}
.btn-outline{border:2px solid var(--navy);color:var(--navy);background:var(--white)}
.btn-navy{background:var(--navy);color:var(--white)}

/* header */
.brand{left:147px;top:8px;display:flex;align-items:center;gap:12px}
.brand-mark{width:66px;height:66px;border-radius:50%;background:var(--blue)}
.brand-name{font-weight:700;font-size:24px;line-height:27px;color:var(--navy);text-transform:uppercase}
.top-phone{left:706px;top:10px;display:flex;align-items:center;gap:10px;font-size:19px;font-weight:500;color:var(--ink)}
.top-phone .dot{width:28px;height:28px;border-radius:50%;background:var(--blue);display:flex;align-items:center;justify-content:center}
.main-nav{left:603px;top:62px;font-size:14px;font-weight:500;color:var(--ink)}
.main-nav a{position:absolute;white-space:nowrap;color:var(--ink);text-decoration:none}
.main-nav .active::after{content:"";position:absolute;left:0;right:-2px;top:21px;height:3px;background:var(--blue);border-radius:2px}

/* hero */
.hero-art{left:0;top:99px}
.hero-title{left:0;width:1200px;top:188px;text-align:center;font-size:55px;color:var(--white);text-shadow:0 3px 8px rgba(0,0,0,.45)}
.hero-sub{left:0;width:1200px;top:266px;text-align:center;font-size:20px;font-weight:500;color:var(--white);text-shadow:0 2px 5px rgba(0,0,0,.5)}
.hero-btn{left:516px;top:322px;width:167px;height:48px;border:2px solid var(--white);background:var(--blue);color:var(--white)}
.slider-dot{left:1123px;width:10px;height:10px;border-radius:50%;background:var(--white)}
.slider-dot.on{background:var(--blue);border:2px solid var(--white)}

/* about */
.ring{border-radius:50%}
.about-title{left:590px;top:770px;font-size:48px}
.about-copy{left:590px;top:846px;width:461px;font-size:14px;line-height:25.7px;text-align:justify;color:var(--text)}

/* services */
.services-title{left:0;width:1200px;top:1364px;text-align:center;font-size:48px}
.service-card{background:var(--white);border-radius:8px;box-shadow:0 6px 18px rgba(20,40,80,.18);text-align:center}
.service-card.featured{background:var(--blue)}
.service-photo{position:absolute;left:6px;top:6px;right:6px;height:213px}
.service-icon{position:absolute;left:50%;width:66px;height:66px;margin-left:-33px;border-radius:50%;background:var(--blue);border:3px solid var(--white);display:flex;align-items:center;justify-content:center}
.featured .service-icon{background:var(--navy)}
.service-name{position:absolute;left:0;right:0;font-size:18px;font-weight:500;color:var(--ink)}
.featured .service-name{color:var(--white)}
.service-text{position:absolute;left:18px;right:18px;font-size:13.5px;line-height:20.5px;color:var(--muted)}
.featured .service-text{color:var(--white)}
.service-card .btn{left:50%;width:132px;margin-left:-66px;height:40px}
.featured .btn{background:var(--blue);color:var(--white);border-color:var(--white)}
.arrow-btn{width:44px;height:44px;border-radius:50%;border:1.5px solid #7b8794;background:rgba(255,255,255,.6);display:flex;align-items:center;justify-content:center}

/* testimonials */
.reviews-title{left:0;width:1200px;top:2132px;text-align:center;font-size:48px}
.review-box{border:1px solid #d9dee4;background:var(--white)}
.avatar{width:108px;height:108px;border-radius:50%}
.review-quote{width:263px;font-size:14px;line-height:19.7px;font-style:italic;color:var(--text);text-align:justify}
.review-name{font-size:16px;font-weight:500;color:var(--blue)}
.stars{font-size:16px;letter-spacing:2px;color:var(--gold)}
.quote-mark{font-family:Georgia,serif;font-size:110px;line-height:1;font-weight:700;color:var(--blue)}

/* contact */
.contact-panel{left:144px;top:2626px;width:912px;height:501px;background:var(--blue);border-radius:6px}
.contact-title{left:0;width:1200px;top:2680px;text-align:center;font-size:52px;color:var(--white)}
.field{position:absolute;background:var(--white);border:1px solid #cfd6de;font:400 15px "Roboto",Arial,sans-serif;color:#5b6168;padding:18px 21px;line-height:16px}

/* footer */
.info{display:flex;align-items:center;gap:14px;color:var(--white)}
.info-icon{width:44px;height:44px;border-radius:50%;border:1.5px solid rgba(255,255,255,.8);display:flex;align-items:center;justify-content:center}
.info-icon.fill{background:var(--blue);border-color:var(--blue)}
.foot-nav{left:0;width:1200px;top:3293px;display:flex;justify-content:center;gap:18px;font-size:16px;font-weight:700;color:var(--white);text-transform:uppercase}
.foot-nav span.sep{color:var(--white);font-size:10px;line-height:20px}
.social{width:36px;height:36px;border-radius:50%;border:2px solid var(--white);background:var(--navy-deep)}
.copyright{left:0;width:1200px;top:3437px;text-align:center;font-size:13px;color:var(--white)}
</style>
</head>
<body>

<!-- Header -->
<div class="abs brand">
  <div class="brand-mark"></div>
  <div class="brand-name">Harbour Lane<br>Removals</div>
</div>
<div class="abs top-phone">
  <span class="dot"><svg width="15" height="15" viewBox="0 0 24 24"><path fill="#fff" d="M6.6 10.8a15.1 15.1 0 0 0 6.6 6.6l2.2-2.2c.3-.3.7-.4 1-.2 1.1.4 2.3.6 3.6.6.6 0 1 .4 1 1V20c0 .6-.4 1-1 1A17 17 0 0 1 3 4c0-.6.4-1 1-1h3.5c.6 0 1 .4 1 1 0 1.3.2 2.5.6 3.6.1.3 0 .7-.2 1z"/></svg></span>
  +1 555 014 2290
</div>
<a class="btn btn-solid" style="left:906px;top:4px;width:148px;height:41px;font-size:13px">Request a quote</a>
<nav class="abs main-nav">
  <a class="active" style="left:0">HOME</a>
  <a style="left:77px">ABOUT US</a>
  <a style="left:183px">SERVICES</a>
  <a style="left:287px">NEWS</a>
  <a style="left:363px">CONTACT US</a>
</nav>

<!-- Hero -->
<svg class="abs hero-art" width="1200" height="620" viewBox="0 0 1200 620">
  <defs>
    <linearGradient id="heroSky" x1="0" y1="0" x2="0" y2="1">
      <stop offset="0" stop-color="#2e5f95"/>
      <stop offset=".45" stop-color="#6f8fb0"/>
      <stop offset=".75" stop-color="#b98a5c"/>
      <stop offset="1" stop-color="#6b5a4a"/>
    </linearGradient>
  </defs>
  <path role="img" aria-label="City skyline at sunset" fill="url(#heroSky)" d="M0 0H1200V400Q600 740 0 400Z"/>
  <path fill="#0a9de2" d="M0 400Q600 740 1200 400V412Q600 800 0 412Z"/>
</svg>
<h1 class="abs heading hero-title">Harbour Lane Removals</h1>
<p class="abs hero-sub">Sed ut perspiciatis unde omniuoluptatem accusantium</p>
<a class="btn hero-btn">Request a quote</a>
<span class="abs slider-dot" style="top:318px"></span>
<span class="abs slider-dot on" style="top:336px;left:1122px;width:12px;height:12px"></span>
<span class="abs slider-dot" style="top:357px"></span>

<!-- About -->
<div class="abs ring" style="left:147px;top:767px;width:380px;height:380px;border:5px solid var(--blue)"></div>
<div class="abs ring" role="img" aria-label="Movers carrying boxes from a van" style="left:160px;top:780px;width:354px;height:354px;background:linear-gradient(150deg,#dfe3e8,#a7b2c0 45%,#b28a63)"></div>
<div class="abs ring" style="left:77px;top:961px;width:140px;height:140px;background:var(--white);border:4px solid var(--navy)"></div>
<div class="abs ring" role="img" aria-label="Two movers with boxes" style="left:86px;top:970px;width:122px;height:122px;background:linear-gradient(160deg,#cfd7e4,#5d6fa6 60%,#b48f66)"></div>
<div class="abs ring" style="left:353px;top:1006px;width:186px;height:186px;background:var(--white);border:4px solid var(--navy)"></div>
<div class="abs ring" role="img" aria-label="Packed boxes on a floor" style="left:363px;top:1016px;width:166px;height:166px;background:linear-gradient(150deg,#5f7a56,#b5b8bf 55%,#9c7f62)"></div>
<h2 class="abs heading about-title">About us</h2>
<p class="abs about-copy">Sed ut perspiciatis unde omnis iste natus error sit voluptatem accusantium doloremque laudantium, totam rem aperiam, eaque ipsa quae ab illo inventore veritatis et quasi architecto beatae vitae dicta sunt explicabo. Nemo enim ipsam voluptatem quia voluptas sit aspernatur aut odit aut fugit, sed quia consequuntur magni dolores eos qui ratione voluptatem sequi nesciunporro ipsum quia dolor sitSed ut perspiciatis unde omnis iste natus error sit voluptatem accusantium doloremque laudantium, totam rem aperiam, eaque ipsa quae ab illo inventore veritatis et quasi architecto beatae vitae dicta sunt explicabo.</p>
<a class="btn btn-solid" style="left:590px;top:1099px;width:134px;height:45px">Read more</a>

<!-- Services -->
<svg class="abs" style="left:0;top:1150px" width="1200" height="1000" viewBox="0 0 1200 1000">
  <defs>
    <linearGradient id="servicesBg" x1="0" y1="0" x2="1" y2="1">
      <stop offset="0" stop-color="#dbe4ec"/>
      <stop offset=".5" stop-color="#eef3f7"/>
      <stop offset="1" stop-color="#d3dde6"/>
    </linearGradient>
  </defs>
  <path role="img" aria-label="Faded photo of movers at work" fill="url(#servicesBg)" d="M0 13Q600 217 1200 13V972Q600 782 0 972Z"/>
  <path fill="none" stroke="#0a9de2" stroke-width="3" d="M0 13Q600 217 1200 13"/>
  <path fill="none" stroke="#0a9de2" stroke-width="3" d="M0 972Q600 782 1200 972"/>
</svg>
<h2 class="abs heading services-title">Our services</h2>

<div class="abs arrow-btn" style="left:64px;top:1677px"><svg width="14" height="14" viewBox="0 0 14 14"><path d="M9 1L3 7l6 6" fill="none" stroke="#333" stroke-width="1.6"/></svg></div>
<div class="abs arrow-btn" style="left:1091px;top:1677px"><svg width="14" height="14" viewBox="0 0 14 14"><path d="M5 1l6 6-6 6" fill="none" stroke="#333" stroke-width="1.6"/></svg></div>

<div class="abs service-card" style="left:144px;top:1458px;width:287px;height:439px">
  <div class="service-photo" role="img" aria-label="Two movers lifting a sofa" style="background:linear-gradient(135deg,#e7e9ec,#9a9ea5 55%,#d7dbe0)"></div>
  <div class="service-icon" style="top:182px"><svg width="34" height="28" viewBox="0 0 34 28" fill="none" stroke="#fff" stroke-width="2"><rect x="2" y="8" width="18" height="14"/><path d="M20 12h7l5 5v5H20"/><circle cx="9" cy="24" r="3"/><circle cx="26" cy="24" r="3"/></svg></div>
  <div class="service-name" style="top:264px">Nemo enim ipsam</div>
  <div class="service-text" style="top:295px">Lorem ipsum dolor sit amet, consectetur adipiscing elit, sed do eiusmod tempor incididunts aute irure dolo</div>
  <a class="btn btn-outline" style="top:377px">Read more</a>
</div>

<div class="abs service-card featured" style="left:456px;top:1458px;width:287px;height:467px">
  <div class="service-photo" style="top:20px;height:213px;background:#fff;left:5px;right:5px"></div>
  <div class="service-photo" role="img" aria-label="Mover wheeling boxes from a truck" style="top:22px;left:8px;right:8px;height:208px;background:linear-gradient(120deg,#5d7d4c,#9fb0a0 50%,#5b4e42)"></div>
  <div class="service-icon" style="top:198px"><svg width="34" height="28" viewBox="0 0 34 28" fill="none" stroke="#fff" stroke-width="2"><rect x="2" y="8" width="18" height="14"/><path d="M20 12h7l5 5v5H20"/><circle cx="9" cy="24" r="3"/><circle cx="26" cy="24" r="3"/></svg></div>
  <div class="service-name" style="top:280px">Neque porro qui</div>
  <div class="service-text" style="top:312px">Lorem ipsum dolor sit amet, consectetur adipiscing elit, sed do eiusmod tempor incididunts aute irure dolo</div>
  <a class="btn btn-outline" style="top:393px">Read more</a>
</div>

<div class="abs service-card" style="left:769px;top:1458px;width:285px;height:439px">
  <div class="service-photo" role="img" aria-label="Movers carrying a piano" style="background:linear-gradient(135deg,#8fa58a,#7b5a3e 50%,#7d8aa6)"></div>
  <div class="service-icon" style="top:182px"><svg width="34" height="28" viewBox="0 0 34 28" fill="none" stroke="#fff" stroke-width="2"><rect x="2" y="8" width="18" height="14"/><path d="M20 12h7l5 5v5H20"/><circle cx="9" cy="24" r="3"/><circle cx="26" cy="24" r="3"/></svg></div>
  <div class="service-name" style="top:264px">Eexercitationem</div>
  <div class="service-text" style="top:295px">Lorem ipsum dolor sit amet, consectetur adipiscing elit, sed do eiusmod tempor incididunts aute irure dolo</div>
  <a class="btn btn-outline" style="top:377px">Read more</a>
</div>

<!-- Testimonials -->
<h2 class="abs heading reviews-title">What customers say</h2>
<div class="abs arrow-btn" style="left:83px;top:2318px"><svg width="14" height="14" viewBox="0 0 14 14"><path d="M9 1L3 7l6 6" fill="none" stroke="#333" stroke-width="1.6"/></svg></div>
<div class="abs arrow-btn" style="left:1072px;top:2318px"><svg width="14" height="14" viewBox="0 0 14 14"><path d="M5 1l6 6-6 6" fill="none" stroke="#333" stroke-width="1.6"/></svg></div>

<div class="abs avatar" role="img" aria-label="Customer portrait" style="left:145px;top:2286px;background:radial-gradient(circle at 50% 40%,#c9a68c,#8d7463 60%,#e6e6e6)"></div>
<p class="abs review-quote" style="left:275px;top:2262px">"Sed ut perspiciatis unde omnis iste natus error sit voluptatem accusantium doloremque laudantium, totam rem aperiam, eaque ipsa quae ab illo inventore veritatis et quasi architecto beatae vitae dicta sunt explicabo"</p>
<div class="abs review-name" style="left:275px;top:2400px">- Marisa</div>
<div class="abs stars" style="left:346px;top:2400px">★★★★★</div>
<div class="abs quote-mark" style="left:512px;top:2374px">”</div>

<div class="abs review-box" style="left:667px;top:2245px;width:382px;height:190px"></div>
<div class="abs avatar" role="img" aria-label="Customer portrait" style="left:610px;top:2286px;background:radial-gradient(circle at 50% 40%,#c8a08a,#4a3530 55%,#c2185b 80%,#eee)"></div>
<p class="abs review-quote" style="left:740px;top:2262px">"Sed ut perspiciatis unde omnis iste natus error sit voluptatem accusantium doloremque laudantium, totam rem aperiam, eaque ipsa quae ab illo inventore veritatis et quasi architecto beatae vitae dicta sunt explicabo"</p>
<div class="abs review-name" style="left:739px;top:2400px">- Marisa</div>
<div class="abs stars" style="left:810px;top:2400px">★★★★★</div>
<div class="abs quote-mark" style="left:977px;top:2374px">”</div>

<a class="btn btn-solid" style="left:497px;top:2494px;width:205px;height:45px;font-size:13.5px">Load more reviews</a>

<!-- Contact -->
<svg class="abs" style="left:0;top:2600px" width="1200" height="906" viewBox="0 0 1200 906">
  <defs>
    <linearGradient id="footBg" x1="0" y1="0" x2="0" y2="1">
      <stop offset="0" stop-color="#1a2b74"/>
      <stop offset="1" stop-color="#0c1850"/>
    </linearGradient>
  </defs>
  <path role="img" aria-label="Faint night city skyline" fill="url(#footBg)" d="M0 128Q600 360 1200 128V906H0Z"/>
</svg>
<div class="abs contact-panel"></div>
<h2 class="abs heading contact-title">Contact us</h2>
<input class="field" style="left:234px;top:2774px;width:359px;height:53px" placeholder="First Name">
<input class="field" style="left:605px;top:2774px;width:360px;height:53px" placeholder="Last Name">
<input class="field" style="left:234px;top:2839px;width:359px;height:53px" placeholder="Email address">
<input class="field" style="left:605px;top:2839px;width:360px;height:53px" placeholder="Phone Number">
<textarea class="field" style="left:234px;top:2905px;width:731px;height:114px;resize:none" placeholder="Message"></textarea>
<a class="btn btn-navy" style="left:520px;top:3045px;width:160px;height:46px;font-size:13.5px">Submit message</a>

<!-- Footer -->
<div class="abs info" style="left:186px;top:3194px">
  <span class="info-icon"><svg width="14" height="18" viewBox="0 0 14 18"><path fill="none" stroke="#fff" stroke-width="1.6" d="M7 17s6-6 6-10A6 6 0 0 0 1 7c0 4 6 10 6 10z"/><circle cx="7" cy="7" r="2" fill="#fff"/></svg></span>
  <span style="font-size:14px;line-height:24px">314,At vero eos et accu<br>samus et iusto odio dimos ducimu</span>
</div>
<div class="abs info" style="left:528px;top:3194px">
  <span class="info-icon fill"><svg width="18" height="18" viewBox="0 0 24 24"><path fill="#fff" d="M6.6 10.8a15.1 15.1 0 0 0 6.6 6.6l2.2-2.2c.3-.3.7-.4 1-.2 1.1.4 2.3.6 3.6.6.6 0 1 .4 1 1V20c0 .6-.4 1-1 1A17 17 0 0 1 3 4c0-.6.4-1 1-1h3.5c.6 0 1 .4 1 1 0 1.3.2 2.5.6 3.6.1.3 0 .7-.2 1z"/></svg></span>
  <span style="font-size:18px;font-weight:500">+ 1 555 014 2290</span>
</div>
<div class="abs info" style="left:789px;top:3194px">
  <span class="info-icon"><svg width="18" height="14" viewBox="0 0 18 14"><rect x="1" y="1" width="16" height="12" rx="1" fill="#fff"/><path d="M1 2l8 6 8-6" fill="none" stroke="#1a2b74" stroke-width="1.5"/></svg></span>
  <span style="font-size:15px">hello@harbourlane-mail.com</span>
</div>

<nav class="abs foot-nav">
  <span>Home</span><span class="sep">■</span>
  <span>About us</span><span class="sep">■</span>
  <span>Services</span><span class="sep">■</span>
  <span>News</span><span class="sep">■</span>
  <span>Contact us</span><span class="sep">■</span>
  <span>Privacy policy</span><span class="sep">■</span>
  <span>Terms of use</span>
</nav>

<div class="abs" style="left:144px;top:3388px;width:912px;height:1px;background:rgba(255,255,255,.3)"></div>
<div class="abs social" style="left:488px;top:3362px"></div>
<div class="abs social" style="left:533px;top:3362px"></div>
<div class="abs social" style="left:578px;top:3362px"></div>
<div class="abs social" style="left:623px;top:3362px"></div>
<div class="abs social" style="left:670px;top:3362px"></div>

<p class="abs copyright">© 2024 Harbour Lane Removals.All Rights Reserved &nbsp;|&nbsp; Privacy Policy &nbsp;|&nbsp; Terms of use</p>

</body>
</html>
```